Varnik Holdings — Business Card Design Brief
Overview
Design a double-sided business card for Varnik Holdings that highlights our two service arms: Varnik Communications (telecommunications) and Varnik Energy (business energy solutions). The card should feel smart and stand out when handed to clients.

Objectives
Showcase our areas of specialty clearly.
Reflect the overall Varnik / Varnik Holdings brand while acknowledging both arms.
Explore using both logos (Communications + Energy) or one unified logo, depending on the design.

Deliverables
One double-sided business card design (front + back).

Content & Copy
Front (preferred): Logo: Varnik / Varnik Holdings
Descriptor: Business Communications | Business Energy
Back:My contact details and company details
Core products: Business Mobile • Telephony • Internet • Business Energy Solutions

Brand & Visual Direction
We have a group logo currently tailored more toward telecoms, plus a separate Varnik Energy logo.
Please explore layouts that use both logos or just one, whichever works best.
Color: I wouldn't mind seeing an option using our the Blue/Purple gradient from our website (varnik-example.co.uk), but also open to non-gradient approaches and other colours..

Overall look: Smart, modern, and distinctive.
Format & Print Specs
Double-sided business card format. (Use a standard size

Must-Haves
Front: Varnik wording or Varnik Holdings wording with atleast 1 logo also on front “Business Communications | Business Energy.”

Back: Contact + company details and core products.
A design that stands out while remaining professional.

Nice-to-Have Options
A gradient version using our site’s Blue/Purple gradient.
A non-gradient version.
A dual-logo treatment versus a single-logo treatment.

Thanks
Owen

```html
<!DOCTYPE html>
<html lang="en">
<head>
<meta charset="utf-8">
<title>Varnik Holdings — Business Card</title>
<link href="https://fonts.googleapis.com/css2?family=Montserrat:wght@700;800&family=Roboto:wght@400&display=swap" rel="stylesheet">
<style>
  :root {
    --backdrop: #e4e4e4;
    --card-light: #ffffff;
    --card-dark: #303030;
    --navy: #1b1464;
    --blue: #1a5fd6;
    --sky: #1ba3e0;
    --green: #3aa613;
    --lime: #8dbb0e;
    --text-grey: #4a4a4a;
    --rule: #c8c8c8;
    --white: #ffffff;
  }
  * { box-sizing: border-box; margin: 0; padding: 0; }
  html, body { width: 1200px; height: 1200px; overflow: hidden; }
  body {
    background: var(--backdrop);
    font-family: "Roboto", Arial, sans-serif;
    position: relative;
  }
  .card {
    position: absolute;
    width: 689px;
    height: 393px;
  }
  .card--front { left: 267px; top: 159px; background: var(--card-light); }
  .card--back { left: 262px; top: 654px; background: var(--card-dark); }

  .brand {
    position: absolute;
    display: flex;
    align-items: center;
    gap: 12px;
    font-family: "Montserrat", Arial, sans-serif;
    font-weight: 800;
    letter-spacing: 0.5px;
    line-height: 1;
  }
  .brand__dot { border-radius: 50%; flex: none; }
  .brand--comms { left: 41px; top: 40px; }
  .brand--energy { right: 45px; top: 40px; }
  .brand--front .brand__name { font-size: 40px; color: var(--navy); }
  .brand--front .brand__dot { width: 38px; height: 38px; }
  .brand--comms .brand__dot { background: var(--blue); }
  .brand--energy .brand__dot { background: var(--green); }

  .holder { position: absolute; left: 41px; top: 196px; }
  .holder__name {
    font-family: "Montserrat", Arial, sans-serif;
    font-weight: 700; font-size: 26px; color: var(--navy); letter-spacing: 0.5px;
  }
  .holder__role { font-size: 15px; color: var(--green); margin-top: 4px; }

  .rule { position: absolute; left: 42px; right: 32px; height: 1px; background: var(--rule); }
  .rule--top { top: 255px; }
  .rule--bottom { top: 335px; }

  .contacts { position: absolute; left: 42px; top: 267px; list-style: none; }
  .contacts li {
    display: flex; align-items: center; gap: 10px;
    font-size: 16px; color: var(--text-grey); height: 20.5px;
  }
  .contacts svg { width: 13px; height: 14px; fill: var(--navy); flex: none; }

  .address {
    position: absolute; right: 39px; top: 269px;
    text-align: right; font-size: 16px; color: var(--text-grey); line-height: 20.5px;
    font-style: normal;
  }

  .products {
    position: absolute; left: 42px; right: 38px; top: 350px;
    display: flex; justify-content: space-between; list-style: none;
    font-size: 17.5px; color: var(--blue);
  }
  .products .sep { color: var(--blue); }
  .products .sep--dark { color: #222; }
  .products .product--energy { color: var(--green); }

  .divider {
    position: absolute; left: 354px; top: 83px; width: 1px; height: 226px;
    background: #bdbdbd;
  }
  .arm { position: absolute; top: 120px; width: 300px; text-align: center; }
  .arm--energy { left: 45px; }
  .arm--comms { left: 380px; }
  .arm .brand { position: static; justify-content: center; flex-direction: column; gap: 18px; }
  .arm .brand__dot { width: 90px; height: 90px; }
  .arm--energy .brand__dot { background: var(--green); }
  .arm--comms .brand__dot { background: var(--blue); }
  .arm .brand__name { font-size: 56px; color: var(--white); }
  .arm__descriptor { margin-top: 14px; font-size: 17px; text-transform: uppercase; }
  .arm--energy .arm__descriptor { color: var(--blue); }
  .arm--comms .arm__descriptor { color: var(--lime); letter-spacing: 3px; }
</style>
</head>
<body>
  <section class="card card--front" aria-label="Card front">
    <div class="brand brand--front brand--comms"><span class="brand__dot"></span><span class="brand__name">VARNIK</span></div>
    <div class="brand brand--front brand--energy"><span class="brand__dot"></span><span class="brand__name">VARNIK</span></div>

    <div class="holder">
      <p class="holder__name">ALEX MARLOW</p>
      <p class="holder__role">President</p>
    </div>

    <div class="rule rule--top"></div>

    <ul class="contacts">
      <li><svg viewBox="0 0 24 24" aria-hidden="true"><path d="M6.6 10.8a15.1 15.1 0 0 0 6.6 6.6l2.2-2.2a1 1 0 0 1 1-.25 11.4 11.4 0 0 0 3.6.57 1 1 0 0 1 1 1V20a1 1 0 0 1-1 1A17 17 0 0 1 3 4a1 1 0 0 1 1-1h3.5a1 1 0 0 1 1 1c0 1.25.2 2.45.57 3.6a1 1 0 0 1-.25 1z"/></svg>555-214-8830</li>
      <li><svg viewBox="0 0 24 24" aria-hidden="true"><path d="M7 1h10a2 2 0 0 1 2 2v18a2 2 0 0 1-2 2H7a2 2 0 0 1-2-2V3a2 2 0 0 1 2-2zm0 3v15h10V4z"/></svg>555-367-1942</li>
      <li><svg viewBox="0 0 24 24" aria-hidden="true"><path d="M2 5h20v14H2zm2 2v.5l8 5 8-5V7zm0 2.8V17h16V9.8l-8 5z"/></svg>info@varnik-example.co.uk</li>
    </ul>

    <address class="address">
      4102 Hollis Street<br>
      Halden, Canada 612<br>
      www.varnik-example.co.uk
    </address>

    <div class="rule rule--bottom"></div>

    <ul class="products">
      <li>Business Mobile</li><li class="sep">•</li>
      <li>Telephony</li><li class="sep">•</li>
      <li>Internet</li><li class="sep sep--dark">•</li>
      <li class="product--energy">Business Energy Solutions</li>
    </ul>
  </section>

  <section class="card card--back" aria-label="Card back">
    <div class="arm arm--energy">
      <div class="brand"><span class="brand__dot"></span><span class="brand__name">VARNIK</span></div>
      <p class="arm__descriptor">Business Communications</p>
    </div>
    <div class="divider"></div>
    <div class="arm arm--comms">
      <div class="brand"><span class="brand__dot"></span><span class="brand__name">VARNIK</span></div>
      <p class="arm__descriptor">Business Energy</p>
    </div>
  </section>
</body>
</html>
```